Brell Stone Company Business Cards

Front and Back Business Card - logo and text setup - cool design. I need workable photoshop or illustrator files so I can setup each employee card with design that is created
Updates

Hi everyone, thank you for the great entries. Please no more white and blue cards - there are so many already - black and silver only now please. thanks!

Target Market(s)

Construction Industry - Facility Managers

Industry/Entity Type

Construction

Contact Information for Business Card

I really like contemporary simplistic looks - clean neat....not opposed to seeing some black backrounds

Requirements
Must have
• Logo/website address with design on front only - www.brellstone-example.com (logo attached)
• Back:
• Name/Title/Company Address/Phone/email address
Nice to have
• Cool design
Should not have
• Nothing gimmicky like Fire or Water - since we are a Fire Protection company - it has all been done

```html
<!DOCTYPE html>
<html lang="en">
<head>
<meta charset="utf-8">
<title>Brell Stone Company – Business Cards</title>
<link href="https://fonts.googleapis.com/css2?family=Lato:wght@400;700;900&display=swap" rel="stylesheet">
<style>
  :root {
    --page-bg: #d6d6d6;
    --card-black: #1d1d1d;
    --card-black-edge: #2a2a2a;
    --silver: #9a9a9a;
    --silver-soft: #6e6e6e;
    --paper: #ffffff;
    --navy: #2c3b70;
    --ink: #222222;
    --accent-red: #e8402f;
  }
  * { margin: 0; padding: 0; box-sizing: border-box; }
  html, body {
    width: 1200px; height: 1059px; overflow: hidden;
    background: var(--page-bg);
    font-family: "Lato", Arial, sans-serif;
  }
  .sheet {
    position: relative; width: 1200px; height: 1059px;
  }
  .card {
    position: absolute; left: 180px; width: 840px; height: 480px;
    overflow: hidden;
    box-shadow: 0 6px 18px rgba(0,0,0,0.25);
  }
  .card--front { top: 36px; background: var(--card-black); }
  .card--back  { top: 543px; background: var(--card-black); display: flex; }

  /* Front */
  .front-brand {
    position: absolute; left: 0; right: 0; top: 170px;
    display: flex; align-items: center; justify-content: center; gap: 18px;
  }
  .brand-mark {
    width: 22px; height: 22px; background: var(--silver);
  }
  .brand-name {
    font-weight: 900; font-size: 86px; letter-spacing: -2px;
    color: var(--silver); line-height: 1;
  }
  .front-web {
    position: absolute; left: 0; right: 0; bottom: 70px;
    text-align: center; color: #e6e6e6; font-size: 20px; letter-spacing: 1.5px;
  }

  /* Back */
  .back-brand {
    width: 420px; height: 100%; background: var(--card-black);
    display: flex; align-items: center; justify-content: center; gap: 12px;
  }
  .back-brand .brand-mark { width: 16px; height: 16px; background: var(--navy); }
  .back-brand .brand-name { font-size: 58px; color: var(--navy); letter-spacing: -1px; }

  .back-info {
    position: relative; flex: 1; background: var(--paper);
    padding: 92px 40px 0 52px; color: var(--ink);
  }
  .back-info::after {
    content: ""; position: absolute; top: 0; right: 0; width: 12px; height: 100%;
    background: var(--accent-red);
  }
  .person-name { font-weight: 700; font-size: 30px; color: var(--navy); }
  .person-title { font-size: 20px; margin-top: 4px; }
  .address { font-size: 20px; line-height: 1.3; margin-top: 26px; }
  .contacts { list-style: none; margin-top: 24px; font-size: 19px; }
  .contacts li { display: flex; align-items: center; gap: 14px; line-height: 1.55; }
  .contacts svg { width: 16px; height: 16px; fill: var(--navy); flex: none; }
</style>
</head>
<body>
<main class="sheet">
  <section class="card card--front" aria-label="Card front">
    <div class="front-brand">
      <span class="brand-mark"></span>
      <span class="brand-name">brell stone</span>
    </div>
    <p class="front-web">www.brellstone-example.com</p>
  </section>

  <section class="card card--back" aria-label="Card back">
    <div class="back-brand">
      <span class="brand-mark"></span>
      <span class="brand-name">brell stone</span>
    </div>
    <div class="back-info">
      <h1 class="person-name">Dana Whitfield Moore</h1>
      <p class="person-title">President</p>
      <p class="address">48 Harbor Park Road<br>Millbrook, NY 10000</p>
      <ul class="contacts">
        <li>
          <svg viewBox="0 0 16 16"><path d="M3.2 1.5l2.3 2.6-1.2 1.8c.9 2 2.6 3.7 4.6 4.6l1.8-1.2 2.6 2.3-1.4 2.4C6.6 13.8 2.2 9.4 1 3.1z"/></svg>
          (555) 014-2290
        </li>
        <li>
          <svg viewBox="0 0 16 16"><path d="M1 3h14v10H1z M1.8 3.8L8 9l6.2-5.2" fill="none" stroke="#2c3b70" stroke-width="1.6"/></svg>
          info@brellstone-example.com
        </li>
        <li>
          <svg viewBox="0 0 16 16"><circle cx="8" cy="8" r="6.6" fill="none" stroke="#2c3b70" stroke-width="1.4"/><path d="M1.5 8h13M8 1.4c-2.4 2.6-2.4 10.6 0 13.2M8 1.4c2.4 2.6 2.4 10.6 0 13.2" fill="none" stroke="#2c3b70" stroke-width="1.2"/></svg>
          www.brellstone-example.com
        </li>
      </ul>
    </div>
  </section>
</main>
</body>
</html>
```